New Bicycle shop business card

Hi!
I'm looking for a business card for my new proffesional bike mechanics shop. This shop is only for fixing broken bikes and not selling bikes.
Peferbly a modern and sleek and modern design.
Colors: black, grey, red, white
Information:
Name: Rijwielwerkplaats Vanhoutte
Shop owner: Bart Vanhoutte & Marieke Segers
Website: www.rijwielwerkplaats-vanhoutte.be
Email: info@rijwielwerkplaats-vanhoutte.be
Phone number: +32471902368
Street adres: Kerkweg 46
9940 Bellebeke
Slogan/shop information: Herstellingen van alle merken.
Logo: see files.
Target Market(s)
People who seek a mechanic to fix or upgrade their bikes.
Contact Information for Business Card
Information:
Website: info@rijwielwerkplaats-vanhoutte.be
9940 Bellebeke
Logo: see files.

```html
<!DOCTYPE html>
<html lang="nl">
<head>
<meta charset="utf-8">
<title>Rijwielwerkplaats Vanhoutte – visitekaartje</title>
<link rel="stylesheet" href="https://fonts.googleapis.com/css2?family=Montserrat:wght@800&family=Roboto:wght@400;500&display=swap">
<style>
  :root {
    --brand-red: #d32a3c;
    --ink: #1c1c1e;
    --paper: #f7f7f6;
    --panel: #efefee;
    --grey-line: #b9b9bb;
    --muted: #444448;
    --backdrop: #e6e6e6;
    --white: #ffffff;
  }
  * { box-sizing: border-box; margin: 0; padding: 0; }
  html, body { width: 1200px; height: 852px; overflow: hidden; }
  body {
    background: var(--backdrop);
    display: flex;
    align-items: center;
    justify-content: center;
    gap: 40px;
    font-family: "Roboto", Arial, sans-serif;
  }
  .card {
    width: 540px;
    height: 310px;
    border-radius: 22px;
    position: relative;
    overflow: hidden;
  }

  /* Front */
  .card-front {
    background: var(--brand-red);
    display: flex;
    flex-direction: column;
    align-items: center;
    justify-content: center;
  }
  .brand {
    display: flex;
    flex-direction: column;
    align-items: center;
    gap: 14px;
    margin-top: -20px;
  }
  .brand-dot {
    width: 44px; height: 44px;
    border-radius: 50%;
  }
  .card-front .brand-dot { background: var(--white); }
  .brand-name {
    font-family: "Montserrat", Arial, sans-serif;
    font-weight: 800;
    font-size: 24px;
    line-height: 1.15;
    letter-spacing: 1px;
    text-transform: uppercase;
    text-align: center;
  }
  .card-front .brand-name { color: var(--ink); }
  .front-tagline {
    position: absolute;
    left: 0; right: 0; bottom: 30px;
    display: flex;
    align-items: center;
    justify-content: center;
    gap: 12px;
    color: var(--white);
    font-size: 13px;
  }
  .front-tagline::before, .front-tagline::after {
    content: "";
    width: 36px; height: 2px;
    background: var(--white);
  }

  /* Back */
  .card-back { background: var(--paper); }
  .back-brand {
    position: absolute;
    left: 0; top: 0;
    width: 250px; height: 240px;
    display: flex;
    align-items: center;
    justify-content: center;
  }
  .card-back .brand-dot { background: var(--brand-red); }
  .card-back .brand-name { color: var(--ink); font-size: 19px; }
  .contact-panel {
    position: absolute;
    left: 262px; top: 0; right: 0;
    height: 240px;
    background: var(--panel);
    border-bottom-left-radius: 14px;
    padding: 48px 16px 0 22px;
  }
  .person-name {
    font-family: "Montserrat", Arial, sans-serif;
    font-weight: 800;
    font-size: 17px;
    letter-spacing: 0.5px;
    color: var(--brand-red);
    text-transform: uppercase;
  }
  .person-role { font-size: 11px; color: var(--muted); margin-bottom: 12px; }
  .contact-list { list-style: none; }
  .contact-list li {
    display: flex;
    align-items: center;
    gap: 8px;
    font-size: 12px;
    color: var(--muted);
    line-height: 20px;
  }
  .contact-list svg { width: 11px; height: 11px; fill: var(--brand-red); flex: none; }
  .contact-list .no-icon { padding-left: 19px; }
  .back-rule {
    position: absolute;
    left: 0; right: 0; bottom: 56px;
    height: 4px;
    background: var(--grey-line);
  }
  .back-band {
    position: absolute;
    left: 0; right: 0; bottom: 0;
    height: 52px;
    background: var(--brand-red);
    color: var(--white);
    font-size: 13px;
    display: flex;
    align-items: center;
    justify-content: center;
  }
</style>
</head>
<body>

  <section class="card card-front">
    <div class="brand">
      <span class="brand-dot"></span>
      <p class="brand-name">Rijwielwerkplaats<br>Vanhoutte</p>
    </div>
    <p class="front-tagline">Herstellingen van alle merken</p>
  </section>

  <section class="card card-back">
    <div class="back-brand">
      <div class="brand">
        <span class="brand-dot"></span>
        <p class="brand-name">Rijwielwerkplaats<br>Vanhoutte</p>
      </div>
    </div>

    <div class="contact-panel">
      <h1 class="person-name">Marieke Segers</h1>
      <p class="person-role">Owner</p>
      <ul class="contact-list">
        <li>
          <svg viewBox="0 0 24 24" aria-hidden="true"><path d="M6.6 10.8a15.1 15.1 0 0 0 6.6 6.6l2.2-2.2a1 1 0 0 1 1-.25 11.4 11.4 0 0 0 3.6.57 1 1 0 0 1 1 1V20a1 1 0 0 1-1 1A17 17 0 0 1 3 4a1 1 0 0 1 1-1h3.5a1 1 0 0 1 1 1c0 1.25.2 2.45.57 3.57a1 1 0 0 1-.25 1z"/></svg>
          +32471902368
        </li>
        <li>
          <svg viewBox="0 0 24 24" aria-hidden="true"><path d="M12 2a10 10 0 1 0 0 20 10 10 0 0 0 0-20zm6.9 6h-2.9a15.6 15.6 0 0 0-1.4-3.6A8 8 0 0 1 18.9 8zM12 4c.8 1.2 1.5 2.5 1.9 4h-3.8c.4-1.5 1.1-2.8 1.9-4zM4.3 14a8 8 0 0 1 0-4h3.4a16 16 0 0 0 0 4zm.8 2h2.9c.3 1.3.8 2.5 1.4 3.6A8 8 0 0 1 5.1 16zM8 8H5.1a8 8 0 0 1 4.3-3.6C8.8 5.5 8.4 6.7 8 8zm4 12c-.8-1.2-1.5-2.5-1.9-4h3.8c-.4 1.5-1.1 2.8-1.9 4zm2.3-6H9.7a14.7 14.7 0 0 1 0-4h4.6a14.7 14.7 0 0 1 0 4zm.3 5.6c.6-1.1 1.1-2.3 1.4-3.6h2.9a8 8 0 0 1-4.3 3.6zm1.7-5.6a16 16 0 0 0 0-4h3.4a8 8 0 0 1 0 4z"/></svg>
          www.rijwielwerkplaats-vanhoutte.be
        </li>
        <li>
          <svg viewBox="0 0 24 24" aria-hidden="true"><path d="M3 5h18a1 1 0 0 1 1 1v12a1 1 0 0 1-1 1H3a1 1 0 0 1-1-1V6a1 1 0 0 1 1-1zm1 2.3V17h16V7.3l-8 5.3z M5.2 7 12 11.5 18.8 7z"/></svg>
          info@rijwielwerkplaats-vanhoutte.be
        </li>
        <li class="no-icon">Kerkweg 46 9940 Bellebeke</li>
      </ul>
    </div>

    <div class="back-rule"></div>
    <p class="back-band">Herstellingen van alle merken</p>
  </section>

</body>
</html>
```